Dietary supplement, Clean and simple.

Hi,
I’d like to talk about the project,

About us:
We are a dietary supplement (Vitamins, Minerals, amino acids etc.) company.
The goal is to have about 25 products at the end of this year. However, for this goal to be achieved we need a good label design to make our products represent our company values.
I’ll be here every day supporting your questions, we are fully committed to making the highest/best quality/customer experience possible.

About the design and our values:
- Professional (We are in the industry of professionalism and expertise. I would love to show we are competent at this, Id. Like to have the labels looks like we have done our research.)
- Efficient (White spacing, good use of the space available.)
- Simple (Straight forward, in 5 seconds they have to know what the product they have is/how functions. We’re trying to simplify it for the consumer.
- No distractions (the only visually “distracting” factor can be the vector art.)

The guidelines:
The goal is to have a universal design, with one element that changes (Vector art). I’ll attach a file/multiple files I think can show some visuals on what I’m looking for, and what parts of the design I think are good/bad.

Label size: 69x155mm (Front is 77.5mm)

Design whatever you think fits our image. You’re the design expert, all I care about is that it fits our company standards/image.

Use this color/font.
Font: Sans Serif
Main company color is Mind green #237D62 (Use this color for something in the design.)

What I thought would be cool/might looks ugly, who knows:
1. The front of the label: Should have 1 vector art, preferably in the top right corner. (That looks good in multiple colors. The vector can have multiple areas to color, I would prefer 2 main colors in the vector art. The interchangeable colors are used for multiple kinds of products.)
2. Text/product information on the left. The text that will have to be displayed:
- Product name for instance “Magnesium + B6”
- Description for the product for instance “Magnesium with ginger taste”
- Company name or logo. (Add ® behind it. We are soon to be trademark registered.)
3. We need to show the "daily intake" amount on the front and also the amount in the complete bottle. For instance, “Daily intake 1 capsule, 60 capsules”.
• You don’t have to design the backside of the label. After I chose a design, I’d like to chat and give specific information on what areas need to be assigned where. (Too complex because of the law.)
Updates

Hi, Please make the deadline 31 days total. I want designers to have the time to design. And not be rushed to finish it.

I want to extend the deadline because i feel like a slightly more medical look would be interesting. Hope you can come up with something!!

Target Market(s)

Dietary supplement consumers

Industry/Entity Type

Dietary supplements

Font styles to use
Sans Serif

Colors

Designer to choose colors to be used in the design.

Requirements
Must have
• Trademark icon "®" has to be at the top right after the company logo(text of logo)/name.

```html
<!DOCTYPE html>
<html lang="en">
<head>
<meta charset="utf-8">
<title>Magnesium + B6 Label</title>
<link href="https://fonts.googleapis.com/css2?family=Noto+Sans:wght@400;500;600;700&family=Roboto+Condensed:ital,wght@1,500&display=swap" rel="stylesheet">
<style>
  :root {
    --page-bg: #e8e8e8;
    --label-white: #ffffff;
    --edge-teal: #9cc8bb;
    --mint-green: #237d62;
    --ink: #222222;
    --pill-gold: #c9b62e;
    --accent-light: #dcf3a6;
    --accent-mid: #b4e26a;
  }
  * { margin: 0; padding: 0; box-sizing: border-box; }
  html, body {
    width: 1200px; height: 1200px; overflow: hidden;
    background: var(--page-bg);
    font-family: "Noto Sans", sans-serif;
  }
  .label {
    position: absolute; left: 40px; top: 349px;
    width: 1120px; height: 502px; overflow: hidden;
    background: linear-gradient(90deg, var(--edge-teal) 0%, #e9f3ef 6%, var(--label-white) 14%, var(--label-white) 86%, #e9f3ef 94%, var(--edge-teal) 100%);
  }
  .accent-area {
    position: absolute; left: 0; top: 300px; width: 1120px; height: 202px;
    background: linear-gradient(to top, rgba(180, 226, 106, 0.55) 0%, rgba(220, 243, 166, 0.35) 45%, rgba(255, 255, 255, 0) 100%);
  }
  .brand {
    position: absolute; left: 0; right: 0; top: 82px;
    display: flex; justify-content: center; align-items: center; gap: 10px;
    color: var(--mint-green);
  }
  .brand-dot { width: 20px; height: 20px; border-radius: 50%; background: var(--mint-green); }
  .brand-name { font-weight: 700; font-size: 38px; letter-spacing: 1px; line-height: 1; }
  .brand-reg { font-weight: 700; font-size: 13px; align-self: flex-start; margin-left: -4px; }
  .product-name {
    position: absolute; left: 311px; top: 226px;
    font-weight: 600; font-size: 41px; color: var(--ink); letter-spacing: 0.5px; line-height: 1.2;
  }
  .product-desc {
    position: absolute; left: 312px; top: 283px; height: 30px;
    padding: 0 10px; border-radius: 8px; background: var(--pill-gold);
    font-weight: 500; font-size: 20.5px; line-height: 30px; color: var(--ink);
  }
  .supplement-tag {
    position: absolute; left: 319px; top: 407px;
    font-weight: 500; font-size: 20px; color: var(--ink); letter-spacing: 0.3px;
  }
  .dose { position: absolute; left: 610px; top: 434px; display: flex; align-items: flex-start; }
  .capsule-icon { width: 17px; height: 34px; }
  .count { margin-left: 3px; display: flex; flex-direction: column; }
  .count-number { font-weight: 700; font-size: 28px; line-height: 26px; color: var(--ink); }
  .count-unit { font-size: 8px; line-height: 10px; color: var(--ink); }
  .divider { width: 1px; height: 36px; background: #cccccc; margin: 0 8px; }
  .intake { font-family: "Roboto Condensed", sans-serif; font-style: italic; font-weight: 500; color: var(--ink); }
  .intake-label { font-size: 15px; line-height: 17px; margin-left: 7px; }
  .intake-amount { font-size: 18px; line-height: 20px; }
</style>
</head>
<body>
  <div class="label">
    <div class="accent-area" role="img" aria-label="Soft green flowing wave artwork across the lower part of the label"></div>

    <div class="brand">
      <span class="brand-dot"></span>
      <span class="brand-name">VERDANT CALM</span>
      <span class="brand-reg">®</span>
    </div>

    <h1 class="product-name">MAGNESIUM + B6</h1>
    <p class="product-desc">Magnesium with ginger taste</p>
    <p class="supplement-tag">DIETARY SUPPLEMENT</p>

    <div class="dose">
      <svg class="capsule-icon" viewBox="0 0 17 34" aria-hidden="true">
        <rect x="1" y="1" width="15" height="32" rx="7.5" fill="none" stroke="#222" stroke-width="1.5"/>
        <line x1="1" y1="17" x2="16" y2="17" stroke="#222" stroke-width="1.5"/>
      </svg>
      <div class="count">
        <span class="count-number">60</span>
        <span class="count-unit">CAPSULES</span>
      </div>
      <span class="divider"></span>
      <div class="intake">
        <div class="intake-label">Daily Intake</div>
        <div class="intake-amount">1 CAPSULE</div>
      </div>
    </div>
  </div>
</body>
</html>
```